Web Design Project for a Software & Consulting Company

We have just completed a recent ArtHerdly project for a new logo (see attached).
As the next stage of our rebranding we now require a website re-design to complement the new logo.
Our current site, http://www.corvinsoft.example was built in-house and does not come across as professional as we would like. We supply software and associated services to some of the world’s largest oil companies and we need our site to reflect that level of client.
We will also be posting another design project for brochures, PowerPoint slides and other materials very soon.
We would like designs for…
Home page
Product page
• TZQ
• BLV
• PNJ
Services
News page
About Us page
Contact Us page
Page for mobile devices that gives basic company and product information
Currently the site is small but we intend to increase content to include white papers etc. this should be taken into account when designing the navigation therefore we would prefer navigation through styled text links rather than images.
Colour schemes should broadly be taken from our new logo, where the dark blue and dark green from the left and right sides of the logo are the main colours, but other, brighter accent colours can be used to highlight sections or content.
Dark Blue = C:88, M:55, Y:44, K:28
Dark Green = C:87, M:53, Y:50, K:50
NB: Don’t use the logo on our current site, make sure you use the one attached.
We would prefer the final file format to be a layered PSD.
The site should be clean and professional and communicate the following...
• That we have a great depth and breadth of knowledge about our customers’ business, enabling us to deliver the best systems and solutions.
• That we are a leading provider of cost estimation and control solutions to the oil and gas industry.
• The benefits of our software and consulting services.
• Show that we deliver outstanding customer service and value with a very high level of professionalism
• The site should have no Flash and be able to self-adjust to fit any screen size.
Things to avoid …
• Obvious and clichéd oil industry imagery, no oil rigs
• Cartoon style graphics
Our Background
We are an integrated software and consulting organization specialising in the drilling side of the oil and gas industry. Simply put our software helps companies better understand, predict and communicate the cost of drilling wells.
We have 3 software products and a consulting offering consisting of…
• TZQ - Probabilistic time and cost software
• BLV – Cost tracking and reporting software
• PNJ – (currently known as DrillSavant) – Lessons learned software
• Consulting services
Our systems are in use in over 30 countries with a broad range of clients including: GN, Marovel, Dunt, Koruna, VELO Sirkami, FALUMI and Quintex.
Our current site can be found at www.corvinsoft.example
Our main competitors are
• http://www.drovanic.example/
• http://www.sumbrask.example/
• http://www.kve.example/services/software-solutions/p1-
Our depth of drilling knowledge, quality of software and collaboration with clients differentiate us form the competition.
We strive for very high levels of customer service.
We look forward to receiving your designs!
Updates
Thanks to all the designers who have submitted a design, we appreciate the effort.
We will do our best to give individual feedback on each design but given that many are quite similar we thought we would give some general feedback first.
Nearly all the designs submitted so far have been slight variations on…
-
Top Menu
-
Scrolling Photo Banner
-
4 Columns
-
Body
-
Deep Footer
These designs are well executed but they are basically the same layout as our existing site and while there is nothing inherently wrong with this layout we would like to see some designs that are a bit more innovative and different. We don’t really want just a polished version of our current site.
Thanks again,
CVS
Thanks to everyone who has submitted a design, the response has been great.
We are close to making a decision so if you are intending to submit a design please do it soon, the deadline is only a few days away.
Thanks again.
CVS
Target Market(s)
Mid to high level executives
Industry/Entity Type
Oil And Gas
Look and feel

```html
<!DOCTYPE html>
<html lang="en">
<head>
<meta charset="utf-8">
<title>Corvin Software</title>
<link href="https://fonts.googleapis.com/css2?family=Lato:wght@400;700&family=Arimo:ital,wght@0,400;0,700;1,700&display=swap" rel="stylesheet">
<style>
:root{
  --page:#e6eaf0;
  --teal:#21505f;
  --teal-dark:#163f4c;
  --ink:#1d4556;
  --text:#2a3a42;
  --line:#d3d9df;
  --panel:#e8f7fb;
  --panel-line:#8ccfdc;
  --white:#fff;
}
*{box-sizing:border-box;margin:0;padding:0}
html,body{width:1054px;height:1200px;overflow:hidden}
body{position:relative;background:var(--page);font-family:"Arimo",Arial,sans-serif;color:var(--text)}
a{color:inherit;text-decoration:none}

/* header */
.site-header{position:absolute;left:0;top:0;width:1054px;height:90px;background:var(--page);z-index:5}
.brand{position:absolute;left:153px;top:14px;display:flex;align-items:center;gap:8px}
.brand-mark{width:34px;height:34px;border-radius:50%;background:var(--teal)}
.brand-name{font-family:"Lato",sans-serif;font-weight:700;font-size:19px;color:var(--ink);line-height:1}
.brand-name small{display:block;font-size:8px;letter-spacing:3px;font-weight:400;margin-top:3px}
.main-nav{position:absolute;left:0;top:0;width:1054px;height:90px}
.nav-link{position:absolute;top:44px;font-size:10.5px;line-height:13px;font-weight:700;color:var(--ink)}
.nav-tab{position:absolute;left:496px;top:35px;width:78px;height:30px;background:var(--white);border-top:3px solid var(--teal-dark)}
.nav-tab .nav-link{top:6px;left:8px}
.dropdown{position:absolute;left:496px;top:64px;width:104px;background:var(--white);border-bottom:4px solid var(--teal-dark);padding:8px 10px 6px}
.dropdown-item{display:block;padding:7px 2px 7px 3px;font-size:10.5px;line-height:13px;color:var(--ink);border-bottom:1px solid var(--line)}
.dropdown-item:last-child{border-bottom:0}

/* hero */
.hero{position:absolute;left:0;top:90px;width:1054px;height:353px;background:var(--teal)}
.hero-slide{position:absolute;left:150px;top:15px;width:753px;height:293px;background:linear-gradient(90deg,#f0f1f2,#fff 60%,#f4f5f6);box-shadow:0 12px 20px rgba(0,0,0,.25)}
.hero-visual{position:absolute;left:20px;top:20px;width:360px;height:250px;border-radius:6px;background:radial-gradient(ellipse at 45% 60%,#d9362f 0,#c42a24 35%,#e9c44a 55%,#f1f1f1 75%)}
.hero-title{position:absolute;left:378px;top:88px;width:360px;font-family:"Lato",sans-serif;font-size:27px;line-height:32px;color:var(--ink)}
.hero-title b{font-weight:700}
.hero-dots{position:absolute;left:474px;top:327px;display:flex;gap:12px}
.hero-dots span{width:11px;height:11px;border-radius:50%;background:#8fa6ae}
.hero-dots .on{background:var(--white)}

/* features */
.features{position:absolute;left:150px;top:463px;width:760px;display:flex}
.feature{flex:0 0 196px}
.feature-head{display:flex;align-items:center;gap:14px;height:31px}
.feature-icon{width:31px;height:31px;border-radius:50%;background:var(--teal-dark);display:flex;align-items:center;justify-content:center}
.feature-label{font-size:12px;font-weight:700;color:var(--ink)}
.feature h3{font-size:11.5px;font-weight:700;color:var(--ink);margin:24px 0 14px}
.feature p{font-size:9.8px;line-height:15.2px;width:165px}
.read-more{display:block;margin-top:18px;font-size:10px}
.read-more::before{content:"›";font-weight:700;margin-right:7px}

/* about & clients */
.content{position:absolute;left:0;top:672px;width:1054px;height:391px;background:var(--white);border-top:1px solid var(--line)}
.section-title{font-size:11.5px;font-weight:700;color:var(--ink)}
.about{position:absolute;left:150px;top:22px;width:356px}
.about-visual{position:absolute;left:-8px;top:32px;width:128px;height:116px;border-radius:50%;background:radial-gradient(circle,#fff 30%,#e44 45%,#f3b530 60%,#3aa15a 72%,#3a6ed0 85%,#fff 90%)}
.about-text{position:absolute;left:129px;top:36px;width:226px;font-size:8.6px;line-height:18px;text-align:justify}
.about-text p+p{margin-top:18px}
.clients{position:absolute;left:542px;top:18px;width:362px}
.clients-head{display:flex;align-items:center;gap:12px}
.arrows{position:absolute;right:0;top:4px;font-size:8px;color:var(--ink);letter-spacing:3px}
.client-grid{margin-top:18px;display:grid;grid-template-columns:repeat(3,1fr);border:1px solid #eceef0}
.client{height:75px;display:flex;align-items:center;justify-content:center;gap:6px;box-shadow:inset 0 0 14px #eef0f2;border:1px solid #f1f2f4;font-size:12px;font-weight:700;color:var(--ink)}
.client i{width:10px;height:10px;background:var(--ink);display:inline-block}

.testimonials{position:absolute;left:150px;top:221px;width:754px;height:156px;background:var(--panel);border:1px solid var(--panel-line);padding:20px 22px}
.testimonials .arrows{right:22px;top:26px}
.testimonial-row{display:flex;gap:52px;margin-top:20px}
.testimonial{width:327px;font-size:10.2px;line-height:18px;text-align:justify}
.testimonial cite{display:block;margin-top:17px;font-weight:700;font-style:italic}

/* footer */
.site-footer{position:absolute;left:0;top:1063px;width:1054px;height:137px;background:var(--teal-dark);color:var(--white);font-size:10.2px;line-height:13px}
.footer-col{position:absolute;top:24px}
.footer-col h4{font-size:10.3px;font-weight:700;margin-bottom:12px}
.footer-col p+p{margin-top:12px}
.social{display:flex;gap:5px;margin-bottom:14px}
.social span{width:23px;height:23px;border-radius:50%;background:#dfe7ea;border:2px solid #fff}
.footer-col .links{line-height:17px}
.partner-badge{position:absolute;left:718px;top:28px;width:184px;height:40px;border-radius:4px;background:#2d5866}
</style>
</head>
<body>

<header class="site-header">
  <a class="brand" href="#">
    <span class="brand-mark"></span>
    <span class="brand-name">CORVIN SOFTWARE<small>TECHNOLOGIES</small></span>
  </a>
  <nav class="main-nav">
    <a class="nav-link" href="#" style="left:437px">HOME</a>
    <div class="nav-tab"><a class="nav-link" href="#">PRODUCTS ▾</a></div>
    <div class="dropdown">
      <a class="dropdown-item" href="#">TZQ</a>
      <a class="dropdown-item" href="#">BLV</a>
      <a class="dropdown-item" href="#">PNJ</a>
    </div>
    <a class="nav-link" href="#" style="left:597px">SERVICES</a>
    <a class="nav-link" href="#" style="left:684px">NEWS</a>
    <a class="nav-link" href="#" style="left:751px">ABOUT US</a>
    <a class="nav-link" href="#" style="left:840px">CONTACT US</a>
  </nav>
</header>

<section class="hero">
  <div class="hero-slide">
    <div class="hero-visual" role="img" aria-label="Red toolbox filled with hand tools"></div>
    <h1 class="hero-title">CVS have <b>TOOLS</b> to help companies <b>BETTER</b> manage the <b>BUSINESS</b> of <b>DRILLING</b> Wells.</h1>
  </div>
  <div class="hero-dots"><span></span><span></span><span class="on"></span><span></span><span></span></div>
</section>

<section class="features">
  <article class="feature">
    <div class="feature-head"><span class="feature-icon"><svg width="14" height="12" viewBox="0 0 14 12"><path d="M0 4h7V0l7 6-7 6V8H0z" fill="#fff"/></svg></span><span class="feature-label">PLAN</span></div>
    <h3>Time &amp; Cost Estimation</h3>
    <p>TZQ delivers a standardized, systematic approach to understanding, quantifying and communicating the impact of project risk to all stakeholders.</p>
    <a class="read-more" href="#">Read More</a>
  </article>
  <article class="feature">
    <div class="feature-head"><span class="feature-icon"><svg width="14" height="12" viewBox="0 0 14 12"><path d="M0 4h7V0l7 6-7 6V8H0z" fill="#fff"/></svg></span><span class="feature-label">EXECUTE</span></div>
    <h3>Material &amp; Cost Control</h3>
    <p>Since 1992 BLV has been helping companies optimize their materials and logistics processes and accurately track costs on a daily basis.</p>
    <a class="read-more" href="#">Read More</a>
  </article>
  <article class="feature">
    <div class="feature-head"><span class="feature-icon"><svg width="14" height="12" viewBox="0 0 14 12"><path d="M0 4h7V0l7 6-7 6V8H0z" fill="#fff"/></svg></span><span class="feature-label">LEARN</span></div>
    <h3>Lessons Learned</h3>
    <p>DrillSavant is an advanced lessons learned and knowledge management system for use in the Oil &amp; Gas industry. It's fully searchable and easy to use.</p>
    <a class="read-more" href="#">Read More</a>
  </article>
  <article class="feature">
    <div class="feature-head"><span class="feature-icon"><svg width="16" height="16" viewBox="0 0 16 16"><path d="M8 2a6 6 0 1 1-6 6" fill="none" stroke="#fff" stroke-width="2.4"/><path d="M0 3l5-1 0 5z" fill="#fff"/></svg></span><span class="feature-label">EMBED</span></div>
    <h3>Services &amp; Consulting</h3>
    <p>Software solutions rely on people and processes to deliver results. From analysis through execution we support our clients to improve performance</p>
    <a class="read-more" href="#">Read More</a>
  </article>
</section>

<main class="content">
  <section class="about">
    <h2 class="section-title">A BIT ABOUT US</h2>
    <div class="about-visual" role="img" aria-label="Ring of colourful figures holding hands"></div>
    <div class="about-text">
      <p>Corvin Software have developed and continue to support software in over 30 countries, providing real results to hundreds of drilling operations.</p>
      <p>With decades of hands-on software and well engineering experience, we are uniquely positioned to provide the right solution to our customers.</p>
    </div>
  </section>

  <section class="clients">
    <div class="clients-head">
      <svg width="18" height="15" viewBox="0 0 18 15"><circle cx="6" cy="4" r="3.5" fill="#1d4556"/><path d="M0 15c0-5 2.5-6.5 6-6.5S12 10 12 15z" fill="#1d4556"/><circle cx="12.5" cy="3.5" r="3" fill="#1d4556"/><path d="M13 8c3 0 5 1.5 5 6h-5z" fill="#1d4556"/></svg>
      <h2 class="section-title">OUR CLIENTS</h2>
    </div>
    <span class="arrows">◀▶</span>
    <div class="client-grid">
      <div class="client">Dunt</div>
      <div class="client">Marovel</div>
      <div class="client"><i></i>VELO Sirkami</div>
      <div class="client">FALUMI</div>
      <div class="client">Tarrow</div>
      <div class="client">Ostbrek</div>
    </div>
  </section>

  <section class="testimonials">
    <div class="clients-head">
      <svg width="22" height="19" viewBox="0 0 22 19"><ellipse cx="11" cy="8" rx="9.5" ry="6.8" fill="none" stroke="#1d4556" stroke-width="1.6"/><path d="M6 14l-1 4 5-3" fill="none" stroke="#1d4556" stroke-width="1.6"/><path d="M7 6h8M7 9h6" stroke="#1d4556" stroke-width="1.4"/></svg>
      <h2 class="section-title">CLIENT'S TESTIMONIALS</h2>
    </div>
    <span class="arrows">◀▶</span>
    <div class="testimonial-row">
      <blockquote class="testimonial">Lorem ipsum dolor sit amet, consectetur adipiscing elit. Maecenas ut nulla sapien, at aliquam erat. Sed vitae massa tellus. Aliquam commodo aliquam metus, sed iaculis nibh tempus.<cite>Mara Keld, CEO</cite></blockquote>
      <blockquote class="testimonial">Lorem ipsum dolor sit amet, consectetur adipiscing elit. Maecenas ut nulla sapien, at aliquam erat. Sed vitae massa tellus. Aliquam commodo aliquam metus, sed iaculis nibh tempus.<cite>Mara Keld, CEO</cite></blockquote>
    </div>
  </section>
</main>

<footer class="site-footer">
  <div class="footer-col" style="left:150px">
    <h4>EUROPE</h4>
    <p>18 Fenwick Row<br>Dunmore, DN4 2QT</p>
    <p>Phone:+44(0)1000 555123<br>Email:eu@corvinsoft.example</p>
  </div>
  <div class="footer-col" style="left:314px">
    <h4>NORTH AMERICA</h4>
    <p>740 Larkspan Ave, Suite 210<br>Redmarsh, TX 70911</p>
    <p>Phone:(555) 014 2290<br>Email:us@corvinsoft.example</p>
  </div>
  <div class="footer-col" style="left:498px">
    <h4>FOLLOW US ONLINE</h4>
    <div class="social"><span></span><span></span><span></span><span></span></div>
    <p class="links">Privacy Policy | Terms of Services | Sitemap<br>Copyright © 2013. All Rights Reserved.</p>
  </div>
  <div class="partner-badge" role="img" aria-label="Partner badge"></div>
</footer>

</body>
</html>
```